LLC needs a business card design that emphasizes consulting and expert witness in upstream oil and g

I need a business card design for my company called Obena Field Advisory Group, LLC. My expertise is in oil and gas upstream operations management to optimize performance and also as an expert witness for law firms in oil and gas upstream operations litigation.
The final design should communicate knowledge and hands-on experience as well as trust. (Obena means rope or lasso. Perhaps "Obena" should be in the form of a rope.) I do not like the color green in any shade. My first preference would be some shade of blue.
Industry/Entity Type
Oil And Gas

```html
<!DOCTYPE html>
<html lang="en">
<head>
<meta charset="utf-8">
<title>Obena Field Advisory Group, LLC — Business Card</title>
<link rel="stylesheet" href="https://fonts.googleapis.com/css2?family=Cinzel:wght@600;700&family=Roboto:wght@300;400;700&display=swap">
<style>
  :root {
    --blue: #2a4f9a;
    --blue-deep: #1f3f82;
    --blue-light: #3a63b0;
    --navy-text: #2c4c96;
    --grey-text: #4a5568;
    --rule: #b9c0cc;
    --paper: #ffffff;
    --paper-shade: #eceff3;
    --stage: #e4e6ea;
  }
  * { box-sizing: border-box; margin: 0; padding: 0; }
  html, body { width: 1200px; height: 892px; overflow: hidden; }
  body {
    background: var(--stage);
    font-family: "Roboto", Arial, sans-serif;
    display: flex;
    align-items: center;
    justify-content: center;
    gap: 40px;
  }
  .card {
    position: relative;
    width: 540px;
    height: 309px;
    overflow: hidden;
    background: linear-gradient(180deg, var(--paper) 0%, var(--paper-shade) 100%);
    box-shadow: 0 6px 18px rgba(0,0,0,0.18);
  }
  .card svg.shapes { position: absolute; inset: 0; }

  .dot {
    display: block; border-radius: 50%;
    border: 3px solid var(--navy-text); background: var(--paper);
    flex: none;
  }

  /* ---------- front ---------- */
  .front-brand {
    position: absolute; left: 26px; top: 22px;
    display: flex; align-items: center; gap: 12px;
  }
  .front-brand .dot { width: 52px; height: 52px; }
  .wordmark { color: var(--navy-text); line-height: 1; }
  .wordmark .name {
    font-family: "Cinzel", "Times New Roman", serif; font-weight: 700;
    font-size: 46px; letter-spacing: 1px;
  }
  .wordmark .sub {
    font-family: "Cinzel", "Times New Roman", serif; font-weight: 600;
    font-size: 9.5px; letter-spacing: 0.8px; margin-top: 3px;
  }
  .person {
    position: absolute; left: 34px; top: 112px;
    border-left: 2px solid var(--navy-text); padding-left: 8px;
    color: var(--navy-text);
  }
  .person .full { font-size: 21px; font-weight: 400; }
  .person .role { font-size: 10px; color: var(--grey-text); margin-top: 2px; }

  .contacts {
    position: absolute; left: 236px; top: 96px; width: 290px;
    font-size: 11.5px; color: var(--grey-text); font-weight: 400;
  }
  .contacts .row {
    display: flex; gap: 24px;
    border-top: 1px solid var(--rule);
    padding: 7px 0 6px;
    white-space: nowrap;
  }
  .contacts .row:last-child { border-bottom: 1px solid var(--rule); }

  .icons {
    position: absolute; left: 236px; top: 212px;
    display: flex; gap: 12px;
  }
  .icons svg { width: 22px; height: 22px; }

  .front-badge {
    position: absolute; right: 28px; bottom: 20px;
    width: 78px; height: 68px; background: var(--paper);
    display: flex; align-items: center; justify-content: center;
    font-family: "Roboto", Arial, sans-serif; font-weight: 700;
    font-size: 17px; color: var(--navy-text);
  }

  /* ---------- back ---------- */
  .back-title {
    position: absolute; left: 0; right: 0; top: 42px;
    text-align: center; color: var(--paper);
  }
  .back-title .name {
    font-family: "Cinzel", "Times New Roman", serif; font-weight: 700;
    font-size: 74px; letter-spacing: 3px; line-height: 1;
  }
  .back-title .sub {
    font-family: "Cinzel", "Times New Roman", serif; font-weight: 600;
    font-size: 12px; letter-spacing: 2px; margin-top: 6px;
  }
  .back-mark {
    position: absolute; left: 50%; top: 204px; transform: translateX(-50%);
    display: flex; align-items: center; gap: 10px;
    font-family: "Roboto", Arial, sans-serif; font-weight: 700;
    font-size: 24px; color: var(--navy-text);
  }
  .back-mark .dot { width: 44px; height: 44px; }
</style>
</head>
<body>

  <section class="card card-front" aria-label="Card front">
    <svg class="shapes" width="540" height="309" viewBox="0 0 540 309" aria-hidden="true">
      <defs>
        <linearGradient id="bandFront" x1="0" y1="0" x2="1" y2="1">
          <stop offset="0" stop-color="#3a63b0"/>
          <stop offset="1" stop-color="#1f3f82"/>
        </linearGradient>
      </defs>
      <rect x="0" y="200" width="540" height="109" fill="url(#bandFront)"/>
      <polygon points="0,245 60,245 90,309 0,309" fill="#ffffff"/>
    </svg>

    <div class="front-brand">
      <span class="dot" aria-hidden="true"></span>
      <div class="wordmark">
        <div class="name">OBENA</div>
        <div class="sub">FIELD ADVISORY GROUP, LLC</div>
      </div>
    </div>

    <div class="person">
      <div class="full">Employee name</div>
      <div class="role">Managing Director</div>
    </div>

    <div class="contacts">
      <div class="row"><span>555-0142 2093</span><span>555-0188 7310</span></div>
      <div class="row"><span>www.obenaadvisory.com</span><span>info@obenaadvisory.com</span></div>
      <div class="row"><span>48 Harbor Lane Ave Westfield, NJ 00000</span></div>
    </div>

    <div class="icons" aria-hidden="true">
      <svg viewBox="0 0 22 22"><circle cx="11" cy="11" r="10" fill="none" stroke="#fff" stroke-width="1.2"/><path d="M8 7c0 4 3 7 7 7l1-2-2-1-1 1c-1-.5-2-1.5-2.5-2.5l1-1-1-2z" fill="#fff"/></svg>
      <svg viewBox="0 0 22 22"><circle cx="11" cy="11" r="10" fill="none" stroke="#fff" stroke-width="1.2"/><rect x="6.5" y="7" width="9" height="6.5" fill="none" stroke="#fff" stroke-width="1.2"/><path d="M9 15.5h4" stroke="#fff" stroke-width="1.2"/></svg>
      <svg viewBox="0 0 22 22"><circle cx="11" cy="11" r="10" fill="none" stroke="#fff" stroke-width="1.2"/><path d="M11 16s-3.5-3.6-3.5-6a3.5 3.5 0 0 1 7 0c0 2.4-3.5 6-3.5 6z" fill="#fff"/><circle cx="11" cy="10" r="1.2" fill="#2a4f9a"/></svg>
    </div>

    <div class="front-badge">Obena</div>
  </section>

  <section class="card card-back" aria-label="Card back">
    <svg class="shapes" width="540" height="309" viewBox="0 0 540 309" aria-hidden="true">
      <defs>
        <linearGradient id="bandBack" x1="0" y1="0" x2="1" y2="1">
          <stop offset="0" stop-color="#1f3f82"/>
          <stop offset="1" stop-color="#3a63b0"/>
        </linearGradient>
      </defs>
      <rect x="0" y="0" width="540" height="172" fill="url(#bandBack)"/>
      <line x1="0" y1="22" x2="540" y2="22" stroke="#ffffff" stroke-opacity="0.55" stroke-width="1"/>
      <line x1="0" y1="150" x2="540" y2="150" stroke="#ffffff" stroke-opacity="0.55" stroke-width="1"/>
      <polygon points="170,309 215,272 270,309" fill="#2a4f9a"/>
    </svg>

    <div class="back-title">
      <div class="name">OBENA</div>
      <div class="sub">FIELD ADVISORY GROUP, LLC</div>
    </div>

    <div class="back-mark">
      <span class="dot" aria-hidden="true"></span>
      <span>Obena</span>
    </div>
  </section>

</body>
</html>
```